Flyer-Design für Küchenmöbellack
Zielgruppe
Wir sind ein Online Shop und vertreiben verschiedene Lacke zur Sanierung von Fliesen, Küchenmöbeln, Badewannen usw.
www.torvalin-lackwerk.de
Jetzt benötigen wir einen Flyer für die Küchenmöbellacke.
DIN lang (105 x 210 mm) hoch / 4 Seiten
Sind in der Größe aber nicht festgelegt.
Alle Info´s die Sie benötigen finden Sie unter:
https://www.torvalin-lackwerk.com/farben-lacke/kuechenmoebellack/
https://www.torvalin-lackwerk.com/pdf/Technisches-Datenblatt-KUECHENMOEBELLACK.pdf
Wir haben von zwei Kunden Vorher - Nachher Bilder die Sie vielleicht verwenden können.
Wenn Sie noch Informationen benötigen sprechen Sie micht an.
Ich freue mich auf viele, schöne Kreative Vorschläge.
Aufgabenstellung
Der Flyer ansprechend, frisch und zeitgemäß gestaltet sein.

```html
<!DOCTYPE html>
<html lang="de">
<head>
<meta charset="utf-8">
<title>Küchenmöbellack Flyer – Innenseite + Einklapper</title>
<link href="https://fonts.googleapis.com/css2?family=Open+Sans:wght@300;400;600&display=swap" rel="stylesheet">
<style>
  :root {
    --stage: #c4c5c7;
    --paper: #ffffff;
    --brand-red: #ad1132;
    --headline-red: #bd3a42;
    --body: #585858;
    --info-box: #c5d1d6;
    --label: #5a5a5a;
  }
  * { margin: 0; padding: 0; box-sizing: border-box; }
  html, body { width: 1200px; height: 872px; overflow: hidden; }
  body {
    position: relative;
    background: var(--stage);
    font-family: "Open Sans", Arial, sans-serif;
    color: var(--body);
  }
  .view-caption {
    position: absolute; top: 14px; left: 0; width: 1200px;
    text-align: center; font-size: 19px; color: #1d1d1d;
  }
  .panel {
    position: absolute; top: 47px; height: 764px;
    background: var(--paper);
    box-shadow: 4px 4px 6px rgba(0,0,0,.35);
  }
  .panel--inside { left: 241px; width: 364px; }
  .panel--flap { left: 608px; width: 352px; }
  .ink-visual {
    position: absolute; left: 0; top: 0; width: 349px; height: 178px;
    background:
      radial-gradient(ellipse 18% 45% at 22% 55%, #e8306a 0%, rgba(232,48,106,0) 100%),
      radial-gradient(ellipse 20% 40% at 20% 20%, #f7a22b 0%, rgba(247,162,43,0) 100%),
      radial-gradient(ellipse 22% 40% at 45% 30%, #5a4fd0 0%, rgba(90,79,208,0) 100%),
      radial-gradient(ellipse 18% 40% at 62% 45%, #1fa3e0 0%, rgba(31,163,224,0) 100%),
      radial-gradient(ellipse 20% 45% at 82% 35%, #9bd22b 0%, rgba(155,210,43,0) 100%),
      radial-gradient(ellipse 14% 30% at 90% 10%, #f5d020 0%, rgba(245,208,32,0) 100%),
      #fff;
  }
  .kitchen-visual {
    position: absolute; left: 124px; top: 30px; width: 200px; height: 140px;
    background: linear-gradient(180deg, #e4e4e4 0%, #f4f4f4 50%, #cfd6d8 75%, #8f8f8f 100%);
    border: 4px solid #fff;
    box-shadow: 2px 3px 6px rgba(0,0,0,.35);
    transform: rotate(4deg);
  }
  .headline {
    position: absolute; top: 207px; font-weight: 400; white-space: nowrap;
  }
  .panel--inside .headline { left: 47px; color: var(--brand-red); }
  .panel--flap .headline { left: 36px; color: var(--headline-red); }
  .headline .small { font-size: 20.6px; }
  .headline .large { font-size: 31px; }
  .headline .line { display: block; line-height: 37px; }
  .headline .line:first-child { line-height: 31px; }
  .body-copy {
    position: absolute; top: 331px; font-weight: 300; white-space: nowrap; color: #4f4f4f;
  }
  .panel--inside .body-copy { left: 47px; font-size: 11px; line-height: 18px; }
  .panel--flap .body-copy { left: 36px; font-size: 11px; line-height: 16.4px; }
  .shop-url {
    position: absolute; color: var(--brand-red); font-weight: 600; font-size: 16px;
  }
  .panel--inside .shop-url { left: 47px; top: 700px; }
  .info-box {
    position: absolute; left: 14px; top: 537px; width: 324px; height: 212px;
    background: var(--info-box);
  }
  .info-box .intro { position: absolute; left: 22px; top: 14px; font-size: 11px; font-weight: 300; line-height: 16px; color: #4f4f4f; }
  .info-box .shop-url { left: 22px; top: 55px; font-size: 16px; }
  .set-title { position: absolute; left: 22px; top: 87px; font-size: 11px; font-weight: 600; color: var(--label); }
  .finish-list { position: absolute; left: 22px; top: 109px; display: flex; gap: 5px; list-style: none; }
  .finish { width: 66px; text-align: center; font-size: 11px; font-weight: 600; color: var(--label); line-height: 12px; }
  .finish .swatch { display: block; width: 66px; height: 55px; margin-bottom: 9px; }
  .swatch--matt { background: linear-gradient(135deg, #e23b3b, #f4d21f 35%, #2f7fd6 65%, #e04a9b); }
  .swatch--silk { background: linear-gradient(135deg, #f5d62b, #7ecb2e 35%, #e33b6d 65%, #f08a24); }
  .swatch--gloss { background: linear-gradient(135deg, #2b6fd0, #e53b3b 40%, #f2c82a 70%, #ef7d25); }
  .swatch--ral { background: linear-gradient(135deg, #ffffff 20%, #f2a23a 45%, #4aa4d8 65%, #ffffff 85%); }
</style>
</head>
<body>
  <p class="view-caption">Ein mal aufgeklappt: 1. Innenseite + Einklapper</p>

  <section class="panel panel--inside">
    <div class="ink-visual" role="img" aria-label="Farbwolken aus bunter Tinte in Rot, Orange, Violett, Blau, Grün und Gelb"></div>
    <h1 class="headline">
      <span class="line small">Küchenmöbellack – mit</span>
      <span class="line large">kleinem Aufwand</span>
      <span class="line"><span class="large">tolle Effekte</span> <span class="small">erzielen</span></span>
    </h1>
    <p class="body-copy">
      Wenn die Küchenmöbel noch voll funktionsfähig<br>
      sind, aber die Farbe langweilig geworden ist oder der<br>
      eine oder andere Kratzer den Möbeln zugesetzt hat,<br>
      wird es Zeit für einen neuen Look.<br>
      Oft ist es nicht möglich, eine neue Küche zu kaufen,<br>
      weil das nicht in das finanzielle Konzept passt.<br>
      Dann kann ein neuer Anstrich mit Küchenmöbellack<br>
      Wunder wirken.<br>
      Ob frisches Soft-Orange, Rot oder intensives Schwarz,<br>
      jeder Farbwunsch ist erfüllbar. Wer sich gar nicht<br>
      zwischen den vielen Möglichkeiten entscheiden kann,<br>
      gestaltet die Küchenoberflächen zwei- oder mehrfarbig<br>
      oder wählt ein klassisches Weiß, der Kreativität sind<br>
      kaum Grenzen gesetzt und das Ergebnis wird Familie<br>
      und Besucher begeistern.<br>
      Der Neuanstrich mit einer attraktiven Farbe macht<br>
      besonders Spaß, wenn er zu zweit oder gemeinsam<br>
      mit Freunden erfolgt. Die Arbeit geht dann schneller<br>
      und der Erfolg der Aktion ist schneller zu sehen.
    </p>
    <p class="shop-url">www.torvalin-lackwerk.com</p>
  </section>

  <section class="panel panel--flap">
    <div class="kitchen-visual" role="img" aria-label="Foto einer weißen Küchenzeile mit blauen, grünen und roten Fronten"></div>
    <h2 class="headline">
      <span class="line small">Mit Küchenmöbellack die</span>
      <span class="line"><span class="small">Küche in</span> <span class="large">frischem Glanz</span></span>
      <span class="line"><span class="large">erstrahlen</span> <span class="small">lassen</span></span>
    </h2>
    <p class="body-copy">
      Im Sortiment der Torvalin-Lackwerk finden Sie Küchen-<br>
      möbellack in mehr als 100 verschiedenen Farbtönen.<br>
      Die Spanne reicht von einem zarten Beige bis zu einem<br>
      eleganten Saphirblau. So fällt es leicht, die eigene<br>
      Traumküche individuell und kreativ zu gestalten.<br>
      Ganz gleich, ob Sie alle Möbel in Ihrer Lieblingsfarbe<br>
      streichen oder farbliche Kontraste setzen – das Ergeb-<br>
      nis kann sich sehen lassen. Die Küchenmöbelfarbe haf-<br>
      tet hervorragend auf beschichteten Oberflächen und<br>
      ist nach dem Trocknen wieder genauso strapazierfähig.<br>
      Nach dem Streichen sehen Ihre Küchenmöbel wieder<br>
      wie neu aus.
    </p>
    <div class="info-box">
      <p class="intro">Besuchen Sie unseren Online-Shop und finden Sie<br>DIE Trendfarbe für Ihre Küche!</p>
      <p class="shop-url">www.torvalin-lackwerk.com</p>
      <p class="set-title">Küchenmöbellack Set in:</p>
      <ul class="finish-list">
        <li class="finish"><span class="swatch swatch--matt" role="img" aria-label="Offene Farbdosen in bunten Tönen"></span>matt</li>
        <li class="finish"><span class="swatch swatch--silk" role="img" aria-label="Offene Farbdosen in bunten Tönen"></span>seiden-<br>glänzend</li>
        <li class="finish"><span class="swatch swatch--gloss" role="img" aria-label="Offene Farbdosen in bunten Tönen"></span>glänzend</li>
        <li class="finish"><span class="swatch swatch--ral" role="img" aria-label="Farbfächer mit RAL-Tönen und Farbdose"></span>RAL-Farben</li>
      </ul>
    </div>
  </section>
</body>
</html>
```